diesel mechanic business card design

granite diesel is a new and upcoming business we are looking for some bad ass designs to help get us started we offer 24 hour road service, off road recovery, welding and custom fabrications we are diesel mechanics so our design should be bold and eye catching flames wrenches engine parts are cool we work in an industrial environment around heavy trucks and equipment this in not a quick grease we fix it all nothing is to big or to small the colors red and black are always a plus but we are open to anything you guys can come up with ready set go

Target Market(s)

other small business primarily trucking and transportation companys

Industry/Entity Type

Business

Contact Information for Business Card

company name Granitte diesel truck & trailer repair / address 14 rear north halloway ave taylor PA 18503 / ownersAdam DeLuccie 570-555-0143 / Walter Dombrosky 570-555-0178 E mail brentkovalsky@mailbox-example.com fax 570-555-0192

Requirements
Nice to have
• industrial modern design
Should not have
• rainbows butterfly's unicorns or cupcakes

```html
<!DOCTYPE html>
<html lang="en">
<head>
<meta charset="utf-8">
<title>Granitte diesel truck &amp; trailer repair – business card</title>
<link rel="stylesheet" href="https://fonts.googleapis.com/css2?family=Ubuntu:wght@400;500;700&display=swap">
<style>
  :root {
    --brand-red: #d3303c;
    --band-red: #c8283a;
    --ink: #1d1d1f;
    --paper: #ffffff;
    --paper-shade: #f1f1f1;
    --rule: #c9c9c9;
    --backdrop: #e7e4df;
  }
  * { box-sizing: border-box; margin: 0; padding: 0; }
  html, body {
    width: 1200px; height: 885px; overflow: hidden;
    background: var(--backdrop);
    font-family: "Ubuntu", sans-serif;
    color: var(--ink);
  }
  .canvas {
    position: relative; width: 1200px; height: 885px;
    display: flex; flex-direction: column; align-items: center; justify-content: center; gap: 48px;
  }
  .card {
    position: relative; width: 560px; height: 320px;
    background: linear-gradient(160deg, var(--paper) 40%, var(--paper-shade));
    box-shadow: 0 6px 18px rgba(0,0,0,.18);
    overflow: hidden;
  }

  /* Business name: one colour, one weight */
  .brand {
    display: flex; align-items: flex-start;
  }
  .brand-mark {
    flex: none; background: var(--brand-red);
  }
  .brand-name {
    font-weight: 500; color: var(--ink); line-height: 1.15;
  }

  /* Front */
  .card-front .brand {
    position: absolute; left: 36px; top: 120px; width: 240px; gap: 12px;
  }
  .card-front .brand-mark { width: 14px; height: 14px; margin-top: 6px; }
  .card-front .brand-name { font-size: 22px; }

  .divider {
    position: absolute; left: 296px; top: 40px; width: 1px; height: 200px;
    background: var(--rule);
  }
  .contacts { position: absolute; left: 318px; top: 58px; width: 220px; }
  .contact { margin-bottom: 10px; }
  .contact-name { color: var(--brand-red); font-weight: 500; font-size: 18px; line-height: 1.1; }
  .contact-phone { display: flex; align-items: center; gap: 6px; font-size: 15px; line-height: 1.3; }
  .contact-phone svg { width: 12px; height: 12px; flex: none; }
  .address { font-weight: 700; font-size: 15px; line-height: 1.35; margin-top: 8px; }

  .info-band {
    position: absolute; left: 0; right: 0; bottom: 0; height: 44px;
    background: var(--band-red); color: var(--paper);
    display: flex; align-items: center; justify-content: space-between;
    padding: 0 22px; font-size: 15px;
  }
  .info-band strong { font-weight: 700; }

  /* Back */
  .card-back .brand {
    position: absolute; left: 70px; top: 50%; transform: translateY(-50%);
    width: 430px; gap: 20px;
  }
  .card-back .brand-mark { width: 26px; height: 26px; margin-top: 12px; }
  .card-back .brand-name { font-size: 42px; }
</style>
</head>
<body>
<main class="canvas">
  <section class="card card-front" aria-label="Business card front">
    <div class="brand">
      <span class="brand-mark" aria-hidden="true"></span>
      <div class="brand-name">Granitte diesel truck &amp; trailer repair</div>
    </div>
    <div class="divider"></div>
    <div class="contacts">
      <div class="contact">
        <div class="contact-name">Brent Kovalsky</div>
        <div class="contact-phone">
          <svg viewBox="0 0 12 12" aria-hidden="true"><rect width="12" height="12" rx="1.5" fill="#1d1d1f"/><path d="M3.4 2.6l1.3 1.6-.7.9c.5 1.1 1.3 1.9 2.4 2.4l.9-.7 1.6 1.3-.9 1.2C5.5 9 3 6.5 2.2 3.5z" fill="#fff"/></svg>
          <span>570-555-0143</span>
        </div>
      </div>
      <div class="contact">
        <div class="contact-name">Walter Dombrosky</div>
        <div class="contact-phone">
          <svg viewBox="0 0 12 12" aria-hidden="true"><rect width="12" height="12" rx="1.5" fill="#1d1d1f"/><path d="M3.4 2.6l1.3 1.6-.7.9c.5 1.1 1.3 1.9 2.4 2.4l.9-.7 1.6 1.3-.9 1.2C5.5 9 3 6.5 2.2 3.5z" fill="#fff"/></svg>
          <span>570-555-0178</span>
        </div>
      </div>
      <div class="address">14 rear north halloway ave<br>millbrook OH 44999</div>
    </div>
    <div class="info-band">
      <span><strong>fax:</strong> 570-555-0192</span>
      <span><strong>E mail:</strong> brentkovalsky@mailbox-example.com</span>
    </div>
  </section>

  <section class="card card-back" aria-label="Business card back">
    <div class="brand">
      <span class="brand-mark" aria-hidden="true"></span>
      <div class="brand-name">Granitte diesel truck &amp; trailer repair</div>
    </div>
  </section>
</main>
</body>
</html>
```